business card deign

Logo needs the following on it.
1. attached logo
2. Tagline - "Cold drinks, loud tunes and good times...we bring it all!"
3. Name- Dalton Pikes, Founder and CPO
4. Address - 412 E. Carver Avenue, Ste 2207, Tampa, FL. 33917
5. Phone - 555.318.4726

```html
<!DOCTYPE html>
<html lang="en">
<head>
<meta charset="utf-8">
<title>Kestrel Business Card</title>
<link href="https://fonts.googleapis.com/css2?family=Montserrat:wght@400;600;700&display=swap" rel="stylesheet">
<style>
  :root {
    --backdrop: #3b3b3b;
    --card: #202020;
    --card-edge: #2a2a2a;
    --ink-light: #f4f4f4;
    --ink-soft: #d6d6d6;
    --ink-gloss: #0b0b0b;
    --rule: #8a8a8a;
    --mark-dark: #141414;
    --mark-light: #f4f4f4;
  }
  * { margin: 0; padding: 0; box-sizing: border-box; }
  html, body {
    width: 1200px; height: 900px; overflow: hidden;
    background: var(--backdrop);
    font-family: "Montserrat", Arial, sans-serif;
  }
  .canvas { position: relative; width: 1200px; height: 900px; }
  .card {
    position: absolute; left: 260px; width: 680px; height: 400px;
    background: var(--card);
    border: 1px solid var(--card-edge);
    border-radius: 30px;
    box-shadow: 0 10px 28px rgba(0,0,0,.45);
  }
  .card--front { top: 35px; }
  .card--back { top: 465px; }

  /* front */
  .front-mark {
    position: absolute; left: 310px; top: 150px; width: 60px; height: 60px;
    border-radius: 50%;
    background: var(--mark-dark);
  }
  .front-brand {
    position: absolute; left: 0; right: 0; top: 235px; text-align: center;
    font-weight: 700; font-size: 42px; letter-spacing: 14px; color: var(--ink-gloss);
  }
  .tagline {
    position: absolute; left: 0; right: 0; bottom: 42px; text-align: center;
    font-size: 16px; color: var(--ink-soft);
  }

  /* back */
  .back-mark {
    position: absolute; left: 150px; top: 170px; width: 60px; height: 60px;
    border-radius: 50%;
    background: var(--mark-light);
  }
  .back-brand {
    position: absolute; left: 40px; top: 255px; width: 280px; text-align: center;
    font-weight: 700; font-size: 38px; letter-spacing: 12px; color: var(--ink-light);
  }
  .divider {
    position: absolute; left: 350px; top: 70px; width: 1px; height: 250px;
    background: var(--rule);
  }
  .contact { position: absolute; left: 378px; top: 72px; color: var(--ink-light); }
  .contact__name { font-weight: 700; font-size: 24px; }
  .contact__role { font-size: 14px; color: var(--ink-soft); margin-top: 2px; }
  .contact__address { font-size: 14px; color: var(--ink-soft); margin-top: 24px; line-height: 1.35; }
  .contact__list { list-style: none; margin-top: 18px; }
  .contact__item {
    display: flex; align-items: center; gap: 12px;
    font-size: 15px; color: var(--ink-soft); margin-bottom: 10px;
  }
  .contact__icon { width: 16px; height: 16px; fill: var(--ink-light); flex: none; }
</style>
</head>
<body>
<main class="canvas">
  <section class="card card--front">
    <div class="front-mark"></div>
    <div class="front-brand">KESTREL</div>
    <p class="tagline">Cold drinks, loud tunes and good times...we bring it all</p>
  </section>

  <section class="card card--back">
    <div class="back-mark"></div>
    <div class="back-brand">KESTREL</div>
    <div class="divider"></div>
    <div class="contact">
      <h1 class="contact__name">Dalton Pikes</h1>
      <p class="contact__role">Founder and CPO</p>
      <p class="contact__address">412 E. Carver Avenue, Ste 2207,<br>Tampa, FL. 33917</p>
      <ul class="contact__list">
        <li class="contact__item">
          <svg class="contact__icon" viewBox="0 0 24 24"><path d="M6.6 10.8a15.1 15.1 0 0 0 6.6 6.6l2.2-2.2c.3-.3.7-.4 1-.2 1.1.4 2.3.6 3.6.6.6 0 1 .4 1 1V20c0 .6-.4 1-1 1A17 17 0 0 1 3 4c0-.6.4-1 1-1h3.5c.6 0 1 .4 1 1 0 1.3.2 2.5.6 3.6.1.3 0 .7-.2 1z"/></svg>
          555.318.4726
        </li>
        <li class="contact__item">
          <svg class="contact__icon" viewBox="0 0 24 24"><path d="M2 5h20v14H2z M3 6l9 7 9-7" fill="none" stroke="#f4f4f4" stroke-width="2"/><path d="M2 5h20l-10 8z"/></svg>
          info@kestrelgoods.com
        </li>
        <li class="contact__item">
          <svg class="contact__icon" viewBox="0 0 24 24"><circle cx="12" cy="12" r="9" fill="none" stroke="#f4f4f4" stroke-width="2"/><path d="M3 12h18M12 3c3 3 3 15 0 18M12 3c-3 3-3 15 0 18" fill="none" stroke="#f4f4f4" stroke-width="1.6"/></svg>
          www.kestrelgoods.com
        </li>
      </ul>
    </div>
  </section>
</main>
</body>
</html>
```